Brell Stone Company Business Cards

Front and Back Business Card - logo and text setup - cool design. I need workable photoshop or illustrator files so I can setup each employee card with design that is created
Updates

Hi everyone, thank you for the great entries. Please no more white and blue cards - there are so many already - black and silver only now please. thanks!

Target Market(s)

Construction Industry - Facility Managers

Industry/Entity Type

Construction

Contact Information for Business Card

I really like contemporary simplistic looks - clean neat....not opposed to seeing some black backrounds

Requirements
Must have
• Logo/website address with design on front only - www.brellstone-example.com (logo attached)
• Back:
• Name/Title/Company Address/Phone/email address
Nice to have
• Cool design
Should not have
• Nothing gimmicky like Fire or Water - since we are a Fire Protection company - it has all been done

```html
<!DOCTYPE html>
<html lang="en">
<head>
<meta charset="utf-8">
<title>Brell Stone Company Business Cards</title>
<link rel="stylesheet" href="https://fonts.googleapis.com/css2?family=Poppins:wght@400;500;700;800&display=swap">
<style>
  :root {
    --canvas-bg: #d6d6d6;
    --card-dark: #323232;
    --card-black: #1f1f1f;
    --silver: #a8a8a8;
    --silver-light: #d4d4d4;
    --silver-mid: #8c8c8c;
    --text-silver: #c2c2c2;
  }
  * { margin: 0; padding: 0; box-sizing: border-box; }
  html, body {
    width: 1200px; height: 1200px; overflow: hidden;
    background: var(--canvas-bg);
    font-family: "Poppins", Arial, sans-serif;
  }
  .sheet { position: relative; width: 1200px; height: 1200px; }
  .card {
    position: absolute; left: 150px;
    width: 900px; height: 514px;
    border-radius: 36px;
    box-shadow: 0 10px 30px rgba(0,0,0,0.22);
    overflow: hidden;
  }
  /* Front card */
  .card-front { top: 66px; background: var(--card-dark); }
  .front-name {
    position: absolute; left: 0; right: 0; top: 170px;
    text-align: center;
    font-weight: 800; font-size: 96px; letter-spacing: -2px;
    color: var(--silver); line-height: 1;
  }
  .front-web {
    position: absolute; left: 0; right: 0; top: 330px;
    text-align: center;
    font-size: 22px; letter-spacing: 1px; color: var(--silver-mid);
  }
  .front-web .accent { color: var(--silver-light); }

  /* Back card */
  .card-back { top: 620px; background: var(--card-black); }
  .back-name {
    position: absolute; left: 60px; top: 270px;
    font-weight: 800; font-size: 64px; letter-spacing: -1px;
    color: var(--silver); line-height: 1;
  }
  .divider {
    position: absolute; left: 470px; top: 100px;
    width: 0; height: 270px;
    border-left: 3px dashed var(--silver-mid);
  }
  .contact {
    position: absolute; left: 505px; top: 96px;
    color: var(--text-silver);
  }
  .person-name {
    font-weight: 700; font-size: 28px; color: var(--silver-light);
    letter-spacing: 0.5px; line-height: 1.2;
  }
  .person-title, .address { font-size: 19px; line-height: 1.65; }
  .lines { list-style: none; margin-top: 4px; }
  .lines li {
    display: flex; align-items: center; gap: 14px;
    font-size: 19px; line-height: 1.7;
  }
  .lines svg { width: 18px; height: 18px; flex: none; }
</style>
</head>
<body>
<main class="sheet">
  <section class="card card-front" aria-label="Card front">
    <div class="front-name">Brell Stone</div>
    <div class="front-web">www.<span class="accent">brellstone-example</span>.com</div>
  </section>

  <section class="card card-back" aria-label="Card back">
    <div class="back-name">Brell Stone</div>
    <div class="divider"></div>
    <div class="contact">
      <div class="person-name">DANA CORWELL</div>
      <div class="person-title">Senior Consultant</div>
      <div class="address">48 Harbor Park Lane<br>Millbrook, NY 12545</div>
      <ul class="lines">
        <li>
          <svg viewBox="0 0 24 24" aria-hidden="true"><path fill="#a8a8a8" d="M6.6 10.8a15.1 15.1 0 0 0 6.6 6.6l2.2-2.2a1 1 0 0 1 1-.25 11.4 11.4 0 0 0 3.6.57 1 1 0 0 1 1 1V20a1 1 0 0 1-1 1A17 17 0 0 1 3 4a1 1 0 0 1 1-1h3.5a1 1 0 0 1 1 1c0 1.25.2 2.45.57 3.57a1 1 0 0 1-.25 1z"/></svg>
          (555) 014-2231
        </li>
        <li>
          <svg viewBox="0 0 24 24" aria-hidden="true"><path fill="#a8a8a8" d="M7 3h10v5H7zM4 9h16a2 2 0 0 1 2 2v6h-4v4H6v-4H2v-6a2 2 0 0 1 2-2zm4 7v3h8v-3z"/></svg>
          (555) 014-2232
        </li>
        <li>
          <svg viewBox="0 0 24 24" aria-hidden="true"><rect x="2.5" y="5" width="19" height="14" rx="1.5" fill="none" stroke="#a8a8a8" stroke-width="2"/><path d="M3 6l9 7 9-7" fill="none" stroke="#a8a8a8" stroke-width="2"/></svg>
          info@brellstone-example.com
        </li>
        <li>
          <svg viewBox="0 0 24 24" aria-hidden="true"><circle cx="12" cy="12" r="10" fill="#a8a8a8"/><path d="M2 12h20M12 2c3 3 3 17 0 20M12 2c-3 3-3 17 0 20" fill="none" stroke="#1f1f1f" stroke-width="1.4"/></svg>
          www.brellstone-example.com
        </li>
      </ul>
    </div>
  </section>
</main>
</body>
</html>
```